Seeking funky, innovative business cards

I am looking to refresh our current business cards to something more engaging, visual and impactful. We are a management consultancy firm, see website (www.larkstone-partners.com.au). I've included our colour scheme, sample of the slides we use and our old business cards. We would like our cards to have icons. The card should display:- Name- Title- Mobile number- Address- Email address- Website - Company logo- Our purpose statement "We build the finest workplaces in the land"

Contact Information for Business Card

Brennan Ulfsson
Consultant
0468 927 341
Level 3, 218 Wexley Street, Melbourne 3000
brennan@larkstone-partners.com.au
www.larkstone-partners.com.au

Purpose statement "We build the finest workplaces in the land"
LOGO available in google images

Font styles to use
Other font styles liked:
• Open Sans Light, Bebas Neue (open to other cool foints)

Colors
ffc214
5c5c5c
f5f5f5
fefefe

Requirements
Must have
• - Name
• - Title
• - Mobile number
• - Address
• - Email address
• - Website
• - Company logo
• - Our purpose statement "We build the finest workplaces in the land"
Nice to have
• - Icons
• - Colour (see our colour scheme"

```html
<!DOCTYPE html>
<html lang="en">
<head>
<meta charset="utf-8">
<title>Larkstone Partners – Business Card</title>
<link rel="stylesheet" href="https://fonts.googleapis.com/css2?family=Lato:wght@400;700&family=Roboto+Condensed:wght@700&display=swap">
<style>
  :root {
    --page-bg: #e9e9e9;
    --card-dark: #444a4b;
    --card-light: #ffffff;
    --accent: #f6c21c;
    --text-light: #f5f5f5;
    --text-muted: #dcdcdc;
    --rule: #7b8283;
    --logo-ink: #4a4f50;
  }
  * { margin: 0; padding: 0; box-sizing: border-box; }
  html, body {
    width: 1200px;
    height: 900px;
    overflow: hidden;
    background: var(--page-bg);
    font-family: "Lato", Arial, sans-serif;
  }
  .canvas { position: relative; width: 1200px; height: 900px; }

  .card {
    position: absolute;
    left: 330px;
    width: 557px;
    height: 343px;
    box-shadow: 0 3px 8px rgba(0,0,0,0.25);
  }

  /* Contact side */
  .card-contact {
    top: 90px;
    background: var(--card-dark);
    color: var(--text-light);
    text-align: center;
    padding-top: 82px;
  }
  .person-name {
    font-family: "Roboto Condensed", "Arial Narrow", sans-serif;
    font-weight: 700;
    font-size: 20px;
    line-height: 22px;
    color: var(--accent);
    text-transform: uppercase;
  }
  .person-title {
    font-size: 16px;
    line-height: 18px;
    color: var(--text-muted);
  }
  .rule {
    width: 130px;
    height: 1px;
    background: var(--rule);
    margin: 8px auto 9px;
  }
  .contact-list { list-style: none; font-size: 16px; line-height: 20px; }
  .contact-label { color: var(--accent); font-weight: 700; }
  .address { font-size: 16px; line-height: 20px; font-style: normal; }
  .address .rule { margin-top: 11px; margin-bottom: 12px; }

  /* Brand side */
  .card-brand {
    top: 469px;
    background: var(--card-light);
  }
  .brand-lockup {
    position: absolute;
    left: 0; right: 0;
    top: 150px;
    display: flex;
    align-items: center;
    justify-content: center;
    gap: 14px;
  }
  .brand-dot {
    width: 16px; height: 16px;
    border-radius: 50%;
    background: var(--accent);
  }
  .brand-name {
    font-size: 58px;
    font-weight: 400;
    line-height: 1;
    color: var(--logo-ink);
  }
  .purpose-band {
    position: absolute;
    left: 0; right: 0; bottom: 0;
    height: 50px;
    background: var(--card-dark);
    display: flex;
    align-items: center;
    justify-content: center;
  }
  .purpose-statement {
    font-size: 17px;
    font-weight: 700;
    color: var(--accent);
    text-transform: uppercase;
  }
</style>
</head>
<body>
<main class="canvas">
  <section class="card card-contact" aria-label="Contact side">
    <h1 class="person-name">Brennan Ulfsson</h1>
    <p class="person-title">Consultant</p>
    <div class="rule"></div>
    <ul class="contact-list">
      <li><span class="contact-label">P:</span> 0468 927 341</li>
      <li><span class="contact-label">E:</span> brennan@larkstone-partners.com.au</li>
      <li><span class="contact-label">W:</span> www.larkstone-partners.com.au</li>
    </ul>
    <address class="address">
      <div class="rule"></div>
      Level 3, 218 Wexley Street<br>Melbourne 3000
    </address>
  </section>

  <section class="card card-brand" aria-label="Brand side">
    <div class="brand-lockup">
      <span class="brand-dot"></span>
      <span class="brand-name">Larkstone</span>
    </div>
    <div class="purpose-band">
      <p class="purpose-statement">We build the finest workplaces in the land</p>
    </div>
  </section>
</main>
</body>
</html>
```